Shine Fox Auto Care Business Card

2 side business card design for an auto detailing business

Target Market(s)

Auto detailing

Contact Information for Business Card

Things included

The business name “Shine Fox Auto Care”
Mark Dunrow
(403)271-6094
Kestrel Bay, Sk

Services offered - complete interior& exterior detail
- paint correction & protection
- ceramic coating
- trim restore
- auto carpet & seat cleaning

Requirements
Must have
• Colours that are in my logo

Services offered

My name Mark Dunrow
403-271-6094
Kestrel Bay, Sk

Not too sure in what order for these ?
Website. Shinefoxautocare.com
Instagram Shinefoxautocare
Email. Shinefoxautoac@mailvento.com

```html
<!DOCTYPE html>
<html lang="en">
<head>
<meta charset="utf-8">
<title>Shine Fox Auto Care – Business Card</title>
<link href="https://fonts.googleapis.com/css2?family=Open+Sans:wght@400;600;700&display=swap" rel="stylesheet">
<style>
  :root {
    --stage: #2b2b2d;
    --card: #1c1c1d;
    --red: #a01c21;
    --white: #f2f2f2;
  }
  html, body {
    margin: 0;
    width: 1200px;
    height: 900px;
    overflow: hidden;
    background: var(--stage);
    font-family: "Open Sans", Arial, sans-serif;
  }
  .sheet {
    position: relative;
    width: 1200px;
    height: 900px;
  }
  .card {
    position: absolute;
    left: 240px;
    width: 720px;
    height: 410px;
    background: var(--card);
    box-shadow: 0 10px 30px rgba(0,0,0,.45);
    overflow: hidden;
  }
  .card--back { top: 30px; }
  .card--front { top: 460px; }

  .brand {
    position: absolute;
    display: flex;
    align-items: center;
    gap: 18px;
  }
  .brand__dot {
    width: 78px;
    height: 78px;
    border-radius: 50%;
    border: 9px solid var(--red);
    box-sizing: border-box;
    flex: none;
  }
  .brand__name {
    font-weight: 700;
    font-size: 32px;
    line-height: 1.1;
    letter-spacing: 1px;
    text-transform: uppercase;
    color: var(--white);
    white-space: nowrap;
  }
  .card--back .brand { left: 250px; top: 90px; }
  .card--front .brand { left: 40px; top: 150px; }
  .card--front .brand__name { font-size: 27px; }

  .services {
    position: absolute;
    left: 70px;
    top: 270px;
    width: 600px;
    margin: 0;
    color: var(--white);
    font-size: 17px;
    line-height: 1.6;
  }
  .services .sep { color: var(--red); padding: 0 6px; }

  .divider {
    position: absolute;
    left: 380px;
    top: 80px;
    width: 2px;
    height: 250px;
    background: var(--red);
  }
  .contact {
    position: absolute;
    left: 410px;
    top: 92px;
    color: var(--white);
  }
  .contact__name {
    margin: 0;
    color: var(--red);
    font-weight: 700;
    font-size: 24px;
    text-transform: uppercase;
    letter-spacing: .5px;
  }
  .contact__role {
    margin: 0 0 14px;
    font-size: 18px;
  }
  .contact__list {
    list-style: none;
    margin: 0;
    padding: 0;
    font-size: 16px;
    line-height: 1.75;
  }
  .contact__list li { display: flex; align-items: center; gap: 10px; white-space: nowrap; }
  .icon { width: 14px; height: 14px; flex: none; fill: var(--red); }
  .icon--plain { border-radius: 50%; background: var(--red); width: 12px; height: 12px; margin: 0 1px; }
</style>
</head>
<body>
<main class="sheet">

  <section class="card card--back" aria-label="Card back">
    <div class="brand">
      <span class="brand__dot"></span>
      <span class="brand__name">Shine Fox<br>Auto Care</span>
    </div>
    <p class="services">
      complete interior&amp; exterior detail<span class="sep">•</span>paint correction &amp; protection<br>
      ceramic coating<span class="sep">•</span>trim restore<span class="sep">•</span>auto carpet &amp; seat cleaning
    </p>
  </section>

  <section class="card card--front" aria-label="Card front">
    <div class="brand">
      <span class="brand__dot"></span>
      <span class="brand__name">Shine Fox<br>Auto Care</span>
    </div>
    <div class="divider"></div>
    <div class="contact">
      <p class="contact__name">Mark Dunrow</p>
      <p class="contact__role">President</p>
      <ul class="contact__list">
        <li>
          <svg class="icon" viewBox="0 0 24 24" aria-hidden="true"><path d="M6.6 10.8a15 15 0 0 0 6.6 6.6l2.2-2.2c.3-.3.7-.4 1-.2 1.1.4 2.3.6 3.6.6.6 0 1 .4 1 1V20c0 .6-.4 1-1 1A17 17 0 0 1 3 4c0-.6.4-1 1-1h3.5c.6 0 1 .4 1 1 0 1.3.2 2.5.6 3.6.1.3 0 .7-.2 1z"/></svg>
          403-271-6094
        </li>
        <li>
          <svg class="icon" viewBox="0 0 24 24" aria-hidden="true"><path d="M2 5h20v14H2z M2 5l10 8 10-8" fill="none" stroke="#a01c21" stroke-width="2.4"/></svg>
          Shinefoxautoac@mailvento.com
        </li>
        <li>
          <svg class="icon" viewBox="0 0 24 24" aria-hidden="true"><g fill="none" stroke="#a01c21" stroke-width="2"><circle cx="12" cy="12" r="10"/><ellipse cx="12" cy="12" rx="4.5" ry="10"/><path d="M2 12h20"/></g></svg>
          Shinefoxautocare.com
        </li>
        <li>
          <span class="icon icon--plain"></span>
          Shinefoxautocare
        </li>
        <li>
          <svg class="icon" viewBox="0 0 24 24" aria-hidden="true"><path d="M12 2a7 7 0 0 0-7 7c0 5 7 13 7 13s7-8 7-13a7 7 0 0 0-7-7zm0 9.5A2.5 2.5 0 1 1 12 6.5a2.5 2.5 0 0 1 0 5z"/></svg>
          Kestrel Bay, Sk
        </li>
      </ul>
    </div>
  </section>

</main>
</body>
</html>
```